Business card for denture clinic Veltrimora

We need a new business card with our new logo. We are a denture clinic in New Zealand with our target market being 45+ years old. We would need a space on the back to write our patients next appointment on. We would space for only one appointment rather than a list. We will attach a photo showing an example of this. But of course, we would like to see your twist on this. We want it to be bold and easy to read and a good mixture of professional but modern. We have attached our logo to be used on the card.

Target Market(s)

People aged 45+ needing dentures

Industry/Entity Type

Dental

Contact Information for Business Card

We want our logo on the front and the space to write an appointment on the back. I've attached an example our our old business card showing this. We need to have the technicians details on the front.

Font styles to use
Sans Serif

Colors
0255a3
919191
fbfbfb

Requirements
Must have
• The following details:
• Liam Dorsett BDT, PGDipCDentTech Calverin
• Dental Prosthetist
• Phone numbers: 0800 47 3125
• 09 572 1394
• Email: liam@veltrimora.co.nz
• www.veltrimora.co.nz
• Address: 14 Marlow Crest Road
• Halbrook West
• Auckland 0793
Nice to have
• We would like our business cards to have more than just two colours as we want them to be more vibrant. We have uploaded an example of a business card we liked that showed this.

```html
<!DOCTYPE html>
<html lang="en">
<head>
<meta charset="utf-8">
<title>Veltrimora – Business Card</title>
<link rel="stylesheet" href="https://fonts.googleapis.com/css2?family=Ubuntu:ital,wght@0,400;0,500;0,700;1,400&display=swap">
<style>
  :root {
    --brand-blue: #0a6db5;
    --card-white: #ffffff;
    --back-grey: #7e7576;
    --band-grey: #8a8182;
    --text-grey: #5f5f5f;
    --rule-grey: #9a9a9a;
    --pill-white: #f4f4f4;
    --stage: #ece8e3;
  }
  * { box-sizing: border-box; margin: 0; padding: 0; }
  html, body {
    width: 1200px; height: 987px; overflow: hidden;
    background: var(--stage);
    font-family: "Ubuntu", Arial, sans-serif;
  }
  .canvas { position: relative; width: 1200px; height: 987px; }

  .card {
    position: absolute; left: 293px; width: 615px; height: 351px;
    border-radius: 19px; overflow: hidden;
  }
  .card-front { top: 130px; background: var(--card-white); }
  .card-back  { top: 506px; background: var(--back-grey); }

  /* Front */
  .brand { position: absolute; right: 24px; top: 42px; text-align: right; }
  .brand-square {
    display: block; width: 56px; height: 56px; margin: 0 66px 8px auto;
    background: var(--brand-blue);
  }
  .brand-name {
    font-size: 28px; font-weight: 500; letter-spacing: 1px;
    color: var(--brand-blue); line-height: 1;
  }
  .person { position: absolute; left: 30px; top: 178px; }
  .person-name { font-size: 21px; font-weight: 700; color: var(--brand-blue); }
  .person-credentials { font-size: 16px; font-weight: 500; margin-left: 5px; }
  .person-role { font-size: 17px; color: var(--text-grey); margin-top: 3px; }
  .divider-rule {
    position: absolute; left: 30px; right: 23px; top: 232px;
    height: 1px; background: var(--rule-grey);
  }
  .contact { position: absolute; font-size: 16px; color: var(--text-grey); line-height: 24px; }
  .contact-phones { left: 30px; top: 240px; }
  .contact-label { color: var(--brand-blue); font-weight: 500; }
  .contact-address { right: 23px; top: 244px; text-align: right; line-height: 21px; }
  .contact-web { color: var(--brand-blue); letter-spacing: 1px; margin-top: 4px; }
  .bottom-band { position: absolute; left: 0; bottom: 0; width: 615px; height: 16px; }

  /* Back */
  .back-title {
    position: absolute; top: 42px; width: 100%; text-align: center;
    color: #fff; font-size: 21px; font-weight: 500;
  }
  .back-brand-tile {
    position: absolute; left: 55px; top: 130px; width: 160px; height: 158px;
    background: var(--card-white); border-radius: 3px;
    display: flex; align-items: center; justify-content: center;
  }
  .back-brand-name { font-size: 20px; font-weight: 500; color: var(--back-grey); letter-spacing: 1px; }
  .back-divider {
    position: absolute; left: 237px; top: 130px; width: 1px; height: 163px;
    background: #d9d4d4;
  }
  .appointment-slot {
    position: absolute; left: 258px; top: 188px; width: 307px; height: 42px;
    background: var(--pill-white); border-radius: 21px;
    font-size: 16px; font-style: italic; color: var(--brand-blue);
  }
  .appointment-slot span { position: absolute; top: 11px; }
  .slot-date { left: 22px; }
  .slot-time { left: 163px; }
</style>
</head>
<body>
<main class="canvas">

  <section class="card card-front">
    <div class="brand">
      <span class="brand-square"></span>
      <div class="brand-name">VELTRIMORA</div>
    </div>

    <div class="person">
      <div class="person-name">LIAM DORSETT<span class="person-credentials">BDT, PGDipCDentTech Calverin</span></div>
      <div class="person-role">Dental Prosthetist</div>
    </div>

    <div class="divider-rule"></div>

    <div class="contact contact-phones">
      <div><span class="contact-label">P</span> : 0800 47 3125</div>
      <div><span class="contact-label">C</span> : 09 572 1394</div>
      <div>liam@veltrimora.co.nz</div>
    </div>

    <div class="contact contact-address">
      <div>14 Marlow Crest Road</div>
      <div>Halbrook West, Auckland 0793</div>
      <div class="contact-web">www.veltrimora.co.nz</div>
    </div>

    <svg class="bottom-band" viewBox="0 0 615 16" preserveAspectRatio="none">
      <rect x="0" y="0" width="615" height="16" fill="var(--band-grey)"/>
      <polygon points="0,0 418,0 412,16 0,16" fill="var(--brand-blue)"/>
      <polygon points="418,0 422,0 416,16 412,16" fill="#ffffff"/>
    </svg>
  </section>

  <section class="card card-back">
    <h2 class="back-title">NEXT APPOINTMENT</h2>
    <div class="back-brand-tile"><span class="back-brand-name">VELTRIMORA</span></div>
    <div class="back-divider"></div>
    <div class="appointment-slot"><span class="slot-date">date:</span><span class="slot-time">time:</span></div>
  </section>

</main>
</body>
</html>
```